Business Card Design For A Cajun Seafood Restaurant

We are opening a cajun seafood restaurant in a week. We mainly serve cajun seafood which is orginally from Louisiana. We want design on both sides of a business card. I have menu on the website. You can go to www.reednkettle.example to check out our menu.

Restaurant name: Reed N' Kettle
Phone: +1 (555) 304-7712
Address: 48206 Ludlow Row, #7, Bexmoor Flats, Ca90000
Email: reednkettle@mailbox.example
Website: www.reednkettle.example

Maybe add social media icons (facebook, instagram) if looks nice on the business card.
facebook.com/reednkettle
instagram.com/reednkettle or @reednkettle

Attached is the logo and other business card samples that I like.

```html
<!DOCTYPE html>
<html lang="en">
<head>
<meta charset="utf-8">
<title>Reed N' Kettle — Business Card</title>
<link rel="stylesheet" href="https://fonts.googleapis.com/css2?family=Open+Sans:wght@400;600;700&display=swap">
<style>
  :root {
    --backdrop: #8a8a8a;
    --card: #ffffff;
    --orange: #ff7a00;
    --orange-deep: #e0600a;
    --corn: #ffd84a;
    --ink: #222222;
    --muted: #6a6a6a;
  }
  * { box-sizing: border-box; margin: 0; padding: 0; }
  html, body { width: 1200px; height: 950px; overflow: hidden; }
  body {
    background: var(--backdrop);
    font-family: "Open Sans", Arial, sans-serif;
    display: flex;
    flex-direction: column;
    align-items: center;
    justify-content: center;
    gap: 40px;
  }
  .card {
    position: relative;
    width: 700px;
    height: 400px;
    background: var(--card);
    overflow: hidden;
    box-shadow: 0 10px 28px rgba(0,0,0,0.3);
  }

  /* Front side */
  .card--front {
    display: flex;
    flex-direction: column;
    align-items: center;
    justify-content: center;
    gap: 34px;
    padding-bottom: 30px;
  }
  .brand {
    display: flex;
    align-items: center;
    gap: 14px;
  }
  .brand__mark {
    width: 46px; height: 46px;
    border-radius: 50%;
    background: var(--orange);
  }
  .brand__name {
    font-size: 46px;
    font-weight: 700;
    color: var(--ink);
    letter-spacing: 0.3px;
  }
  .brand__tagline {
    margin-top: -22px;
    font-size: 15px;
    font-weight: 700;
    letter-spacing: 2px;
    text-transform: uppercase;
    color: var(--orange);
  }
  .socials {
    display: flex;
    gap: 20px;
    font-size: 15px;
    color: var(--ink);
  }
  .socials__item { display: flex; align-items: center; gap: 7px; }
  .socials__mark {
    width: 16px; height: 16px;
    border-radius: 50%;
    background: var(--orange);
  }

  /* Back side */
  .card--back { display: block; }
  .artwork {
    position: absolute;
    top: 0; right: 0;
    width: 58%; height: 100%;
    background:
      radial-gradient(ellipse 55% 45% at 40% 32%, var(--corn) 0%, rgba(255,216,74,0.55) 35%, rgba(255,216,74,0) 70%),
      radial-gradient(ellipse 70% 60% at 50% 60%, #ff9a2a 0%, var(--orange) 60%, var(--orange-deep) 100%);
    clip-path: polygon(18% 0, 100% 0, 100% 100%, 0 100%, 4% 55%);
  }
  .details {
    position: relative;
    z-index: 1;
    width: 48%;
    padding: 188px 0 0 44px;
  }
  .details__bar {
    position: absolute;
    left: 0; top: 192px;
    width: 12px; height: 42px;
    background: var(--orange);
  }
  .details__name {
    font-size: 24px;
    font-weight: 600;
    color: var(--orange);
    text-transform: uppercase;
    line-height: 1.15;
  }
  .details__role {
    font-size: 16px;
    color: var(--ink);
    margin-top: 1px;
  }
  .details__address {
    font-size: 15px;
    color: var(--muted);
    line-height: 1.4;
    margin-top: 12px;
    font-style: normal;
  }
  .contact { list-style: none; margin-top: 8px; }
  .contact__item {
    display: flex; align-items: center; gap: 8px;
    font-size: 15px; color: var(--muted); line-height: 1.5;
    white-space: nowrap;
  }
  .contact__icon { width: 14px; height: 14px; flex: none; }
</style>
</head>
<body>

  <section class="card card--front" aria-label="Business card front">
    <div class="brand">
      <span class="brand__mark"></span>
      <span class="brand__name">Reed N' Kettle</span>
    </div>
    <p class="brand__tagline">Cajun Seafood House</p>
    <div class="socials">
      <span class="socials__item"><span class="socials__mark"></span>reednkettle</span>
      <span class="socials__item"><span class="socials__mark"></span>@reednkettle</span>
    </div>
  </section>

  <section class="card card--back" aria-label="Business card back">
    <div class="artwork" role="img" aria-label="Illustrated cartoon crab mascot lifting a cob of corn over its head"></div>
    <div class="details">
      <span class="details__bar"></span>
      <h1 class="details__name">Dana Whitlock</h1>
      <p class="details__role">CEO/Founder</p>
      <address class="details__address">48206 Ludlow Row, #7<br>Bexmoor Flats, Ca90000</address>
      <ul class="contact">
        <li class="contact__item">
          <svg class="contact__icon" viewBox="0 0 16 16"><path fill="#ff7a00" d="M3 1h3l1.5 4-2 1.3a9 9 0 0 0 4.2 4.2L11 8.5l4 1.5v3a2 2 0 0 1-2 2A13 13 0 0 1 1 3a2 2 0 0 1 2-2z"/></svg>
          +1 (555) 304-7712
        </li>
        <li class="contact__item">
          <svg class="contact__icon" viewBox="0 0 16 16"><rect x="1" y="3" width="14" height="10" rx="1.5" fill="#ff7a00"/><path d="M1.5 4l6.5 5 6.5-5" stroke="#fff" stroke-width="1.4" fill="none"/></svg>
          reednkettle@mailbox.example
        </li>
        <li class="contact__item">
          <svg class="contact__icon" viewBox="0 0 16 16"><circle cx="8" cy="8" r="7" fill="#ff7a00"/><path d="M1 8h14M8 1c3 3 3 11 0 14M8 1c-3 3-3 11 0 14" stroke="#fff" stroke-width="1.1" fill="none"/></svg>
          www.reednkettle.example
        </li>
      </ul>
    </div>
  </section>

</body>
</html>
```